Design Woocommerce & Wordpress Pages and emails

**Freelancer Contest Brief: Transform Steadfast KVL’s Digital Landscape**
**Overview:**
We're thrilled to invite talented designers to participate in a contest aimed at revolutionizing the digital assets of Steadfast KVL, a dynamic leader in the precious metals industry. We are seeking innovative designs for high-converting product pages, engaging product landing pages, transactional emails, versatile marketing email templates, a sophisticated sales funnel, and a redesigned homepage, all seamlessly integrated with WooCommerce and WordPress.
**Project Details:**
1. **Homepage Redesign:**
- **Objective:** Create a balanced homepage that caters to our local audience and our expanding eCommerce market.
- **Requirements:**
- Highlight our dual focus as an eCommerce platform and a local business.
- Emphasize our key services: buying jewelry, selling bullion, and coins.
- Design elements should appeal to both online audiences and local customers, effectively communicating our commitment to serving both communities.
- Deliver the design in Figma to ensure a collaborative and feedback-friendly process.
2. **Product Page Design:**
- **Objective:** Craft a sophisticated and contemporary product page that significantly boosts conversion rates by highlighting product details and fostering trust.
- **Requirements:**
- Include comprehensive product specifications, concise and detailed descriptions, and pricing information.
- Incorporate sections for customer testimonials, trust badges, guarantees, and an engaging "About Us" story.
- Preserve essential information from our existing product pages, while enhancing visual appeal, usability, and most importantly, conversion potential.
- Deliver the design in Figma.
3. **Product Landing Page Design:**
- **Objective:** Develop an impactful landing page to showcase 4-10 products, driving user engagement and interest.
- **Requirements:**
- Present a curated selection of products with striking visuals and succinct descriptions.
- Facilitate easy navigation and encourage exploration of individual product pages.
- Optimize this page for incoming traffic from ads on platforms like Facebook, Instagram, Google, and notably X.com.
4. **Account Page Design:**
- Design a user-friendly and intuitive account page that enhances the customer experience and encourages seamless interaction with our platform.
5. **Transactional Email Design:**
- **Objective:** Develop clear and branded email templates for various order statuses, including processing, completed, canceled, and updated with tracking information.
- **Requirements:** Deliver the email templates in HTML format.
6. **Marketing Email Template Design:**
- **Objective:** Create five versatile marketing email templates, including:
- One template for abandoned cart recovery.
- Four templates for product promotions, designed to quickly adapt to market fluctuations with smart posting features.
- **Requirements:** Ensure templates are flexible and able to accommodate rapid changes in our offerings due to market dynamics. Deliver these in HTML format.
7. **Sales Funnel Design:**
- **Objective:** Design a high-converting sales funnel using PL Chutes and TileSmith, following best funnel practices.
- **Requirements:**
- Focus on a one-product promotion with strategic elements including one order bump, one downsell, and one upsell post-checkout.
- Ensure the funnel is optimized for maximum conversion efficiency and seamlessly integrated within our existing platform.
**Specific Needs:**
- Our current product pages lack effective conversion. We require designs that seamlessly blend elegance with modernity, emphasizing product details while subtly integrating persuasive sales pitches and trust-building elements.
- Email templates must be agile, designed to handle promotional changes driven by fluctuations in the gold and silver markets, with specific products going on sale rapidly.
- The design must allow us to quickly assemble product presentations and efficiently dispatch email campaigns to keep pace with the fast-moving market.
- The homepage redesign should effectively balance the needs of our local store visitors and our online shoppers, emphasizing our services in buying jewelry, and selling bullion and coins.
**References:**
- Current Product Page: [Steadfast KVL Product Page](https://steadfastkvl.example/product/1oz-canadian-gold-maple-leaf-ry/)
- Layout Inspiration: [ClickHarbor Example](https://www.clickharbor.example/call-to-action/mr-bramble-ecommerce-product-page) (Note: We draw inspiration from the layout, not the design style.)
**Submission Guidelines:**
- Submit your designs through ArtHive job board.
- Ensure compatibility with WooCommerce and WordPress platforms.
- Provide product and page designs in Figma and email templates in HTML format.
- Include a brief explanation of your design choices and their alignment with our objectives.
our competitors website Korvin.example, tqingot.example, rfingot.example.
Our website URL: steadfastkvl.example
Target Market(s)
investors, and new investors, hedge against inflation, people needing to sell their gold.
Industry/Entity Type
Precious Metals, ecommerce, we buy gold,

```html
<!DOCTYPE html>
<html lang="en">
<head>
<meta charset="utf-8">
<title>My Account – Steadfast KVL Refineries</title>
<link href="https://fonts.googleapis.com/css2?family=Figtree:wght@400;500;600;700;800&display=swap" rel="stylesheet">
<style>
:root{
  --ink:#231f20;
  --ink-soft:#4a4546;
  --gold:#ebbb55;
  --gold-light:#e8d6a9;
  --panel:#f2f2f2;
  --line:#d9d9d9;
  --nav:#ececec;
  --white:#fff;
  --muted:#8a8585;
}
*{box-sizing:border-box;margin:0;padding:0}
html,body{width:886px;height:1200px;overflow:hidden;background:var(--white)}
body{font-family:"Figtree",sans-serif;color:var(--ink)}
.page{position:relative;width:1350px;height:1828px;transform:scale(0.65630);transform-origin:0 0}
.abs{position:absolute}
svg{display:block}

/* top ticker */
.ticker{left:0;top:0;width:1350px;height:48px;background:var(--ink);color:var(--white);font-size:16px}
.ticker .metal{position:absolute;top:14px}
.ticker .metal b{font-weight:700;margin-right:10px}
.ticker .sep{position:absolute;top:13px;width:1px;height:22px;background:#555}
.ticker .phone{position:absolute;left:996px;top:13px;font-size:18px;font-weight:600;display:flex;gap:8px;align-items:center}
.ticker .loc{position:absolute;left:1213px;top:14px;display:flex;gap:6px;align-items:center}

/* header */
.brand{left:60px;top:88px;display:flex;align-items:center;gap:14px;font-size:26px;font-weight:600;letter-spacing:.5px;text-transform:uppercase}
.brand .mark{width:40px;height:40px;border-radius:50%;background:var(--ink)}
.search{left:752px;top:80px;width:421px;height:56px;border:1px solid var(--line);border-radius:28px;overflow:hidden}
.search span{position:absolute;left:32px;top:17px;font-size:16px;color:var(--muted)}
.search .btn{position:absolute;right:0;top:0;width:59px;height:56px;background:linear-gradient(90deg,var(--gold),var(--gold-light));display:flex;align-items:center;justify-content:center}
.cart-count{left:1276px;top:89px;width:14px;height:14px;border-radius:50%;background:var(--gold);color:var(--white);font-size:9px;text-align:center;line-height:14px}

.nav{left:0;top:165px;width:1350px;height:54px;background:var(--nav);display:flex;justify-content:center;align-items:center;font-size:18px;font-weight:500}
.nav a{color:var(--ink);text-decoration:none;padding:0 41px;border-right:1px solid #bbb;line-height:20px}
.nav a:last-child{border-right:0}

.crumbs{left:97px;top:240px;font-size:15px;color:var(--ink-soft)}
.crumbs i{font-style:normal;margin:0 12px}

/* sidebar */
.side{left:100px;top:277px;width:260px;height:272px;border:1.5px solid var(--line);border-radius:8px;padding:26px 21px 0 31px}
.side li{list-style:none;font-size:15px;height:40px;line-height:24px;border-bottom:1px solid var(--line);padding-top:0}
.side li:last-child{border-bottom:0}
.side li.on{color:var(--gold)}

/* main panel */
.panel{left:389px;top:276px;width:861px;height:690px;background:var(--panel);border-radius:16px}
.h1{left:434px;top:310px;font-size:30px;font-weight:700}
.h1 small{font-size:14px;font-weight:400;color:var(--ink-soft);margin-left:4px}
.lead{font-size:14px;line-height:18px;color:var(--ink-soft)}
.rule{height:1px;background:#d6d6d6}
.label{font-size:15px;font-weight:700}
.field{width:274px;height:50px;border:1px solid var(--line);border-radius:8px;background:var(--panel);font-size:15px;color:var(--muted);padding:16px 21px}
.hint{left:728px;top:613px;font-size:10px;color:var(--ink-soft)}
.save{left:435px;top:629px;width:213px;height:61px;border-radius:31px;background:linear-gradient(90deg,var(--gold),var(--gold-light));font-size:15px;font-weight:800;text-align:center;line-height:61px;letter-spacing:.3px}

.email-card{left:414px;top:710px;width:813px;height:230px;border:1.5px solid var(--line);border-radius:10px;background:var(--panel)}
.email-input{left:445px;top:873px;width:317px;height:50px;border:1px solid var(--line);border-radius:8px;overflow:hidden;font-size:15px;color:var(--muted)}
.email-input span{position:absolute;left:22px;top:16px}
.email-input .go{position:absolute;right:0;top:0;width:56px;height:50px;background:var(--gold);display:flex;align-items:center;justify-content:center}

/* contact band */
.band{left:0;top:1012px;width:1350px;height:160px;background:linear-gradient(90deg,var(--gold),var(--gold-light))}
.band .box{position:absolute;top:39px;width:88px;height:84px;border:1.5px solid var(--ink);border-radius:10px;display:flex;align-items:center;justify-content:center}
.band .k{position:absolute;font-size:15px;font-weight:500}
.band .v{position:absolute;font-size:21px;font-weight:700;line-height:25px}

/* footer */
.foot{left:0;top:1171px;width:1350px;height:657px;background:var(--ink);color:var(--white)}
.col{position:absolute;top:82px}
.col h3{font-size:21px;font-weight:700;margin-bottom:26px}
.col li{list-style:none;font-size:14px;line-height:25px;color:#d8d4d4}
.hours{position:absolute;left:975px;top:136px;width:243px;height:84px;border:1px solid #666;border-radius:10px;background:#3a3536;padding:17px 23px;font-size:17px;font-weight:700;line-height:25px}
.about{position:absolute;left:975px;top:241px;width:260px;font-size:13.5px;line-height:20px;color:#d8d4d4}
.frule{position:absolute;left:60px;width:1230px;height:1px;background:#444}
.ready{position:absolute;left:61px;top:471px;font-size:20px;font-weight:700}
.pill{position:absolute;top:464px;width:126px;height:44px;border-radius:22px;font-size:12px;font-weight:800;text-align:center;line-height:44px;color:var(--ink)}
.pill.call{left:388px;background:linear-gradient(90deg,var(--gold),var(--gold-light))}
.pill.visit{left:524px;background:var(--white)}
.social{position:absolute;top:465px;width:42px;height:42px;border-radius:4px;background:#3a3536}
.social.active{background:var(--gold)}
.fbrand{position:absolute;left:0;width:1350px;top:568px;text-align:center;font-size:25px;font-weight:600;text-transform:uppercase;letter-spacing:.5px;display:flex;justify-content:center;align-items:center;gap:14px}
.fbrand .mark{width:40px;height:40px;border-radius:50%;background:var(--white)}
.copy{position:absolute;left:489px;top:611px;font-size:14.5px;color:#d8d4d4}
.chat{position:absolute;left:1232px;top:574px}
</style>
</head>
<body>
<div class="page">

  <div class="abs ticker">
    <div class="metal" style="left:59px"><b>Gold</b>$2,767.69</div>
    <div class="sep" style="left:204px"></div>
    <div class="metal" style="left:235px"><b>Silver</b>$34.89</div>
    <div class="sep" style="left:369px"></div>
    <div class="metal" style="left:400px"><b>Platinum</b>$1,042.35</div>
    <div class="sep" style="left:576px"></div>
    <div class="metal" style="left:606px"><b>Palladium</b>$1,100.30</div>
    <div class="phone">
      <svg width="16" height="16" viewBox="0 0 24 24"><path fill="#ebbb55" d="M6.6 10.8a15.2 15.2 0 0 0 6.6 6.6l2.2-2.2a1 1 0 0 1 1-.25 11.4 11.4 0 0 0 3.6.57 1 1 0 0 1 1 1V20a1 1 0 0 1-1 1A17 17 0 0 1 3 4a1 1 0 0 1 1-1h3.5a1 1 0 0 1 1 1c0 1.25.2 2.45.57 3.57a1 1 0 0 1-.25 1z"/></svg>
      (555) 014-2290
    </div>
    <div class="sep" style="left:1183px"></div>
    <div class="loc">
      <svg width="12" height="15" viewBox="0 0 24 30"><path fill="#ebbb55" d="M12 0a11 11 0 0 0-11 11c0 8 11 19 11 19s11-11 11-19A11 11 0 0 0 12 0zm0 15a4 4 0 1 1 0-8 4 4 0 0 1 0 8z"/></svg>
      Location
    </div>
  </div>

  <div class="abs brand"><div class="mark"></div>Steadfast KVL Refineries</div>

  <div class="abs search">
    <span>Search for product or categories....</span>
    <div class="btn"><svg width="20" height="20" viewBox="0 0 24 24" fill="none" stroke="#231f20" stroke-width="2.6"><circle cx="10.5" cy="10.5" r="6.5"/><path d="M15.5 15.5l5 5"/></svg></div>
  </div>
  <svg class="abs" style="left:1200px;top:91px" width="32" height="34" viewBox="0 0 32 34" fill="none" stroke="#231f20" stroke-width="2.4"><circle cx="16" cy="10" r="8"/><path d="M3 33c0-8 6-13 13-13s13 5 13 13z"/></svg>
  <svg class="abs" style="left:1249px;top:91px" width="36" height="34" viewBox="0 0 36 34" fill="none" stroke="#231f20" stroke-width="2.4"><path d="M1 3h6l4 19h18l4-13H11"/><circle cx="14" cy="29" r="2.5"/><circle cx="27" cy="29" r="2.5"/></svg>
  <div class="abs cart-count">0</div>

  <nav class="abs nav">
    <a>Gold</a><a>Silver</a><a>Shop All</a><a>Deals</a><a>Sell to us</a><a>We Buy</a><a>IRA</a><a>Jewelry</a>
  </nav>

  <div class="abs crumbs">Home<i>/</i>My Account</div>

  <ul class="abs side">
    <li class="on">Account Details</li>
    <li>Address Book</li>
    <li>Orders</li>
    <li>Account Settings</li>
    <li>Make &amp; See Payments</li>
    <li>Packing List Preferences</li>
  </ul>

  <div class="abs panel"></div>
  <div class="abs h1">Account Details <small>Personal Information</small></div>
  <p class="abs lead" style="left:435px;top:358px;width:760px">It is a long established fact that a reader will be distracted by the readable content of a page when looking at its layout. The point of using Lorem Ipsum is that it has a more-or-less normal.</p>
  <div class="abs rule" style="left:427px;top:413px;width:785px"></div>

  <div class="abs label" style="left:434px;top:436px">First name</div>
  <div class="abs field" style="left:435px;top:462px">First Name</div>
  <div class="abs label" style="left:727px;top:436px">Last name</div>
  <div class="abs field" style="left:729px;top:462px">Last name</div>

  <div class="abs label" style="left:433px;top:530px">Birth date</div>
  <div class="abs field" style="left:435px;top:556px">DD/MM/YYYY</div>
  <svg class="abs" style="left:674px;top:572px" width="18" height="18" viewBox="0 0 18 18" fill="none" stroke="#4a4546" stroke-width="1.3"><rect x="1" y="2.5" width="16" height="14.5" rx="1.5"/><path d="M1 6.5h16M5 1v3M13 1v3"/><path d="M4.5 9.5h1M8.5 9.5h1M12.5 9.5h1M4.5 13h1M8.5 13h1M12.5 13h1"/></svg>
  <div class="abs label" style="left:729px;top:530px">Phone Number</div>
  <div class="abs field" style="left:729px;top:556px;color:var(--ink-soft)">123456789</div>
  <div class="abs hint">Keep 9-digit format with no spaces and dashes.</div>

  <div class="abs save">SAVE DETAILS</div>

  <div class="abs email-card"></div>
  <div class="abs" style="left:443px;top:737px;font-size:21px;font-weight:700">Email Address</div>
  <p class="abs lead" style="left:445px;top:768px;width:700px">It is a long established fact that a reader will be distracted by the readable content of a page when looking at its layout. The point of using Lorem Ipsum is that it has a more-or-less normal.</p>
  <div class="abs rule" style="left:443px;top:824px;width:750px"></div>
  <div class="abs label" style="left:443px;top:847px">EMAIL ADDRESS</div>
  <div class="abs email-input">
    <span>email@example.com</span>
    <div class="go"><svg width="16" height="16" viewBox="0 0 24 24"><path fill="#231f20" d="M22 2L2 10l7 3 3 7z"/><path stroke="#ebbb55" stroke-width="1.5" d="M22 2L9 13"/></svg></div>
  </div>

  <div class="abs band">
    <div class="box" style="left:125px"><svg width="28" height="28" viewBox="0 0 24 24"><path fill="#231f20" d="M6.6 10.8a15.2 15.2 0 0 0 6.6 6.6l2.2-2.2a1 1 0 0 1 1-.25 11.4 11.4 0 0 0 3.6.57 1 1 0 0 1 1 1V20a1 1 0 0 1-1 1A17 17 0 0 1 3 4a1 1 0 0 1 1-1h3.5a1 1 0 0 1 1 1c0 1.25.2 2.45.57 3.57a1 1 0 0 1-.25 1z"/></svg></div>
    <div class="k" style="left:232px;top:58px">Phone Number</div>
    <div class="v" style="left:232px;top:81px">(555) 014-2290</div>

    <div class="box" style="left:471px"><svg width="20" height="26" viewBox="0 0 24 30"><path fill="#231f20" d="M12 0a11 11 0 0 0-11 11c0 8 11 19 11 19s11-11 11-19A11 11 0 0 0 12 0zm0 15a4 4 0 1 1 0-8 4 4 0 0 1 0 8z"/></svg></div>
    <div class="k" style="left:577px;top:44px">Location</div>
    <div class="v" style="left:578px;top:68px">420 Larkspur Ave NE,<br>Millbrook, OR 97000</div>

    <div class="box" style="left:892px"><svg width="30" height="22" viewBox="0 0 30 22"><rect width="30" height="22" rx="2" fill="#231f20"/><path d="M2 3l13 10L28 3" fill="none" stroke="#e9c987" stroke-width="2"/></svg></div>
    <div class="k" style="left:1000px;top:58px">Email</div>
    <div class="v" style="left:1000px;top:81px">info@steadfastkvl.example</div>
  </div>

  <footer class="abs foot">
    <div class="col" style="left:140px"><h3>Buying &amp; selling</h3><ul><li>Shop Bullion</li><li>IRA Rollovers</li><li>Silver Bullion</li><li>Gold Bullion</li><li>Platinum Bullion</li><li>Palladium Bullion</li><li>Steadfast Jewelry</li></ul></div>
    <div class="col" style="left:371px"><h3>Company</h3><ul><li>Leave a Review</li><li>Testimonials</li><li>Refinery Process</li><li>Blog</li><li>About Us</li></ul></div>
    <div class="col" style="left:558px"><h3>Legal</h3><ul><li>Privacy Policy</li><li>Terms and Conditions</li><li>Mail-in Terms</li><li>Acceptable Use</li><li>Cookie Policy</li><li>Disclaimer Policy</li><li>Payment Terms</li><li>Shipping Policy</li><li>Returns Policy</li><li>Price Match</li></ul></div>
    <div class="col" style="left:768px"><h3>Customer care</h3><ul><li>My account</li><li>Investment Tools</li><li>Contact us</li><li>FAQs</li><li>Jewelry 101</li><li>Jewelry Repair</li></ul></div>
    <div class="col" style="left:974px"><h3>Opening Hours</h3></div>
    <div class="hours">Open Mon-Fri<br>10:00am - 6:00pm PST</div>
    <p class="about">Steadfast KVL Refineries is a proudly patriotic Christian business in the United States of America.</p>

    <div class="frule" style="top:434px"></div>
    <div class="ready">Our team is ready to serve you!</div>
    <div class="pill call">CALL NOW</div>
    <div class="pill visit">VISIT US</div>
    <div class="social" style="left:1039px"></div>
    <div class="social" style="left:1091px"></div>
    <div class="social active" style="left:1143px"></div>
    <div class="social" style="left:1195px"></div>
    <div class="social" style="left:1247px"></div>
    <div class="frule" style="top:535px"></div>

    <div class="fbrand"><div class="mark"></div>Steadfast KVL Refineries</div>
    <div class="copy">© 2024 All Rights Reserved Steadfast KVL Refineries</div>
    <svg class="chat" width="58" height="52" viewBox="0 0 58 52"><path fill="#ebbb55" d="M33 2c13 0 23 8 23 18s-10 18-23 18c-2 0-4 0-6-1l-10 7 3-10c-6-3-10-8-10-14C10 10 20 2 33 2z"/><path fill="#e8d6a9" d="M12 18C5 20 1 25 1 31c0 4 2 8 6 10l-2 8 8-5c2 .5 4 .8 6 .8 5 0 9-2 12-5-12 0-20-10-19-22z"/><circle cx="27" cy="20" r="3" fill="#231f20"/><circle cx="38" cy="20" r="3" fill="#231f20"/></svg>
  </footer>

</div>
</body>
</html>
```